UI/UX Re-Do for TallyNest - a free to use project management platform for desktop and mobile.

UI/UX Re-Do for TallyNest
TallyNest is a free to use project management platform for desktop and mobile.
We are looking for help with our UI/UX re-design.
As of now the platform is totally functional.
The problem is around flow and look. We want TN to become something that any one can use to manage and even socialize any project. A project can be something work related like organizing a team around a software build, marketing campaign, shared client file space, etc... In fact, most of our current members are using TN for just such work projects.
We also see a project as planning a wedding, organizing a group trip, a simple to-do list, organizing a kids sports team, and so on...
To become a platform that people will use in their work and personal life we first need to become more intuitive and friendly - while maintaining advanced functionality for more advanced needs.
We need help to beautify, streamline, and simplify - while keeping all the functions.
The quickest way to understand TN, and our current issues is this short video:
https://vidlumo.example/w/Qa7KdP2mXzR
For sure see this link for the entire most recent description AND images:
https://tallynestapp.example/?p=HumbZ4KcWrT
The best way to understand TN is to actually use it:
https://tallynestapp.example
Should you choose to take a run at improving TN here are the details:
Please focus your ideas for mobile, it's where we have the biggest issues.
Feel free to get outside the box.
Avoid swipe oriented designs.
Feel free to focus on ideas over polished outputs.
Use any tool you like, PS, hand drawing, written description if you think that works best.
(FYI - we use mostly use Orvane Slides docs internally)
Point is illustration of ideas over tool choice.
Feel free to:
Create something totally new
And/or riff on what we have now
And/or riff on the new design we are considering (see images below)
|||
If we go the direction of the images/designs below the idea is to give people options on how they see/experience TN.
Just below is what we are calling Ground View. This is a more basic and simple flow. Probably a default to keep new users feeling comfortable at the start.
<img src="https://i.picbarn.example/8wNtLQe.jpg" style="width: 100%;">
https://i.picbarn.example/8wNtLQe.jpg
|||
We are calling this optional view Sky View. It is more advanced and can show all project, goal(renamed 'milestones') at the same time. This is more of a paint job on the current design.
<img src="https://i.picbarn.example/vhRmJxd.jpg" style="width: 100%;">
https://i.picbarn.example/vhRmJxd.jpg
|||
If you're submitting please let us know if you can also do the PS files for dev.
Not required, but once we nail down the concepts we want someone to hone in the PS files.
As an optional bonus we will also be giving credit to you/your company in TN.
Let us know if you do or don't want that.
We are excited to see your work!!
<img src=" " style="width: 100%;">
Target Market(s)
Anyone who needs to organize any project, big or small. The key is to make a super friendly user experience for new users while retaining advanced functions.
Industry/Entity Type
Management
Number of Pages Required
2 page

```html
<!DOCTYPE html>
<html lang="en">
<head>
<meta charset="utf-8">
<title>TallyNest Dashboard</title>
<link rel="stylesheet" href="https://fonts.googleapis.com/css2?family=Open+Sans:wght@400;600;700&display=swap">
<style>
:root{
  --navy:#1f4866;
  --navy-dark:#1e3f5a;
  --nav-muted:#9fc0dc;
  --brand:#f59a2b;
  --blue:#3d86e0;
  --grey-btn:#b3b3b3;
  --panel-bg:#ebebeb;
  --card:#ffffff;
  --text:#222;
  --muted:#666;
  --faint:#aaa;
  --green:#5cc08a;
  --alert:#e8523f;
  --line:#e3e3e3;
}
*{box-sizing:border-box;margin:0;padding:0}
html,body{width:1200px;height:675px;overflow:hidden}
body{font-family:"Open Sans",sans-serif;color:var(--text);background:#fff;position:relative}
.abs{position:absolute}
.topbar{left:0;top:0;width:1200px;height:50px;background:var(--navy)}
.brand{left:28px;top:15px;font-size:15px;font-weight:700;color:var(--brand);letter-spacing:.3px}
.nav a{position:absolute;top:20px;font-size:9px;font-weight:600;color:var(--nav-muted);text-decoration:none;letter-spacing:.3px}
.nav a.active{color:#fff}
.badge{left:1159px;top:14px;width:12px;height:12px;border-radius:50%;background:var(--alert);color:#fff;font-size:7px;text-align:center;line-height:12px}
.page-head{left:0;top:50px;width:1200px;height:62px;border-bottom:1px solid var(--line)}
.page-title{left:27px;top:22px;font-size:15px;font-weight:700;letter-spacing:.2px}
.stat{top:16px;width:60px;text-align:center;line-height:1}
.stat b{display:block;font-size:18px;font-weight:700}
.stat span{display:block;font-size:11px;color:#444;margin-top:1px}
.side-btn{left:28px;width:231px;height:37px;color:#fff;font-size:9px;font-weight:700;padding:0 10px;line-height:37px;border-radius:2px}
.side-btn.blue{background:var(--blue)}
.side-btn.grey{background:var(--grey-btn)}
.kit-head{left:278px;top:113px;width:250px;height:37px;background:var(--grey-btn);color:#fff;font-size:8.5px;font-weight:700;line-height:37px;padding-left:38px}
.kit-col{left:278px;top:150px;width:250px;height:525px;border-left:1px solid var(--line)}
.task{left:298px;width:211px;background:var(--card);border:1px solid #e6e6e6;font-size:8.5px;padding:7px 11px}
.meta{position:absolute;left:11px;bottom:8px;font-size:7px;color:#999;display:flex;gap:8px;align-items:center}
.group{left:298px;top:219px;width:211px;height:261px;background:#ececec;border-left:3px solid var(--blue)}
.pill{top:247px;width:47px;height:17px;border-radius:9px;background:var(--green);color:#fff;font-size:7px;text-align:center;line-height:17px}
.sub{left:309px;width:195px;height:38px;background:#f5f5f5;font-size:8.5px;color:var(--faint);padding-left:8px;line-height:38px}
.sub.open{background:#fff;color:#333;box-shadow:0 1px 2px rgba(0,0,0,.08)}
.feed{left:528px;top:113px;width:672px;height:525px;background:var(--panel-bg)}
.post{left:546px;width:625px;background:var(--card)}
.avatar{border-radius:50%;position:absolute}
.name{font-size:8.5px;font-weight:600;color:#111}
.name small{font-weight:400;font-size:8.5px}
.stamp{font-size:8px;color:#555;position:absolute}
.body{font-size:8px;color:#444;line-height:12px}
.reply{font-size:7px;color:#555}
.kebab{position:absolute;width:2px}
.composer{left:528px;top:638px;width:672px;height:37px;background:#fff}
.composer span{position:absolute;left:19px;top:12px;font-size:8.5px;color:#777}
.tool{top:643px;width:24px;height:24px;border-radius:50%;background:var(--navy-dark);border:2px solid #5c7f9c}
</style>
</head>
<body>

<div class="abs topbar"></div>
<div class="abs brand">TALLYNEST</div>
<nav class="nav">
  <a class="active" style="left:462px">DASHBOARD</a>
  <a style="left:539px">MY PROJECTS</a>
  <a style="left:618px">PUBLIC PROJECT</a>
  <a style="left:709px">ADMIN</a>
</nav>
<svg class="abs" style="left:1107px;top:18px" width="14" height="14" viewBox="0 0 14 14"><circle cx="8" cy="6" r="4.5" fill="none" stroke="#fff" stroke-width="1.6"/><path d="M4.7 9.3L1.5 12.5" stroke="#fff" stroke-width="1.8"/></svg>
<svg class="abs" style="left:1150px;top:19px" width="14" height="14" viewBox="0 0 14 14"><path d="M3 10V6a4 4 0 018 0v4l1 1H2z" fill="none" stroke="#fff" stroke-width="1.4"/><path d="M5.5 12.5h3" stroke="#fff" stroke-width="1.4"/></svg>
<div class="abs badge">5</div>

<div class="abs page-head">
  <div class="abs page-title">DASHBOARD</div>
  <div class="abs stat" style="left:951px"><b>5</b><span>Projects</span></div>
  <div class="abs stat" style="left:1022px"><b>42</b><span>Goal</span></div>
  <div class="abs stat" style="left:1082px"><b>76</b><span>Task</span></div>
  <svg class="abs" style="left:1159px;top:25px" width="13" height="11" viewBox="0 0 13 11"><path d="M0 1.5h13M0 5.5h13M0 9.5h13" stroke="var(--navy)" stroke-width="2"/></svg>
</div>

<div class="abs side-btn grey" style="top:125px">All Projects</div>
<div class="abs side-btn blue" style="top:175px">TallyNest Top Project Picks</div>
<div class="abs side-btn blue" style="top:225px">Most Popular Public Projects</div>
<div class="abs side-btn blue" style="top:276px">All Public Projects</div>

<div class="abs kit-col"></div>
<div class="abs kit-head">STARTUP STARTER KITS</div>
<svg class="abs" style="left:296px;top:130px" width="8" height="2"><rect width="8" height="1.4" fill="#fff"/></svg>
<svg class="abs" style="left:500px;top:126px" width="2" height="10"><circle cx="1" cy="1" r="1" fill="#fff"/><circle cx="1" cy="5" r="1" fill="#fff"/><circle cx="1" cy="9" r="1" fill="#fff"/></svg>
<svg class="abs" style="left:519px;top:119px" width="4" height="4"><circle cx="2" cy="2" r="2" fill="var(--green)"/></svg>

<div class="abs task" style="top:162px;height:50px">Meeting Notes / Business SCRUM
  <div class="meta"><span>&#9632; 7</span><span>&#8984; 5</span></div></div>

<div class="abs group"></div>
<div class="abs" style="left:309px;top:224px;font-size:8.5px">Corporate Structure</div>
<div class="abs" style="left:309px;top:251px;font-size:7px;color:#999">&#9632; 12</div>
<div class="abs pill" style="left:404px">JOIN</div>
<div class="abs pill" style="left:456px">COPY</div>
<div class="abs sub" style="top:281px">Financial Model " Compredssion"</div>
<div class="abs sub" style="top:322px">Business Plan "Research"</div>
<div class="abs sub" style="top:362px">Competitive Landscape</div>
<div class="abs sub open" style="top:402px">Incorporation Info</div>
<div class="abs" style="left:377px;top:452px;font-size:7px;color:#888">&#8853; Add Task</div>

<div class="abs task" style="top:488px;height:49px">Meeting Notes / Business SCRUM<div class="meta"><span>&#9632; 7</span></div></div>
<div class="abs task" style="top:545px;height:48px">Fund Raising / Corp Dev<div class="meta"><span>&#9632; 7</span></div></div>
<div class="abs task" style="top:601px;height:49px">Operating Finance<div class="meta"><span>&#9632; 7</span></div></div>
<div class="abs task" style="top:657px;height:30px">Sales / Business Development</div>

<div class="abs feed"></div>

<article class="abs post" style="top:125px;height:212px">
  <div class="avatar" role="img" aria-label="Profile photo of Corin Ashby" style="left:20px;top:12px;width:42px;height:42px;background:radial-gradient(circle at 50% 40%,#d9a25a,#e6b923 70%)"></div>
  <div class="abs name" style="left:80px;top:17px;font-size:12px;font-weight:400">Corin Ashby</div>
  <div class="abs" style="left:80px;top:32px;font-size:8.5px">TN Cases</div>
  <div class="stamp" style="left:481px;top:21px">5/27.2017 &nbsp; 12:21 am EDT</div>
  <svg class="kebab" style="left:755px;top:0;left:578px;top:20px" height="9"><circle cx="1" cy="1" r="1" fill="#888"/><circle cx="1" cy="4.5" r="1" fill="#888"/><circle cx="1" cy="8" r="1" fill="#888"/></svg>
  <div class="avatar" role="img" aria-label="Team member photo" style="left:80px;top:50px;width:20px;height:20px;background:#c9826a"></div>
  <div class="avatar" role="img" aria-label="Team member photo" style="left:102px;top:50px;width:20px;height:20px;background:#8d6a55"></div>
  <div class="avatar" role="img" aria-label="Team member photo" style="left:124px;top:50px;width:20px;height:20px;background:#5a7a5f"></div>
  <div class="avatar" role="img" aria-label="Team member photo" style="left:146px;top:50px;width:20px;height:20px;background:#6f9bb0"></div>
  <div class="avatar" role="img" aria-label="Team member photo" style="left:168px;top:50px;width:20px;height:20px;background:#4a3a34"></div>
  <div class="abs" style="left:80px;top:91px;font-size:8.5px;font-weight:700">This is a good place to use Notes, rather than a Presentation.</div>
  <div class="abs body" style="left:80px;top:115px">Step one for most of us os to research what type of corporate structure to start with...<br>We recommend doing your research with an eye toward the future.<br>Will you be raising money through a VC or angels?<br>Will you have partners?<br>Tax implications?<br>And many other questions. Talk to a CPA and Attorney. Along the way take tons of notes.</div>
</article>

<article class="abs post" style="top:350px;height:162px">
  <div class="avatar" role="img" aria-label="Profile photo of Mara Ellison" style="left:45px;top:17px;width:19px;height:19px;background:#c47a5e"></div>
  <div class="abs name" style="left:75px;top:19px">Mara Ellison - <small>TN Cases</small></div>
  <div class="stamp" style="left:481px;top:20px">5/27.2017 &nbsp; 12:21 am EDT</div>
  <svg class="kebab" style="left:578px;top:19px" height="9"><circle cx="1" cy="1" r="1" fill="#888"/><circle cx="1" cy="4.5" r="1" fill="#888"/><circle cx="1" cy="8" r="1" fill="#888"/></svg>
  <div class="abs body" style="left:75px;top:38px;width:540px">Step one for most of us os to research what type of corporate structure to start with...We recommend doing your research with an eye toward the future. Will you be raising money through a VC or angels? Will you have partners?</div>
  <div class="abs reply" style="left:75px;top:70px">Reply</div>
  <div class="abs" style="left:64px;top:88px;width:540px;height:1px;background:var(--line)"></div>
  <div class="avatar" role="img" aria-label="Profile photo of Tobin Krasowetz" style="left:75px;top:96px;width:19px;height:19px;background:#7e98a4"></div>
  <div class="abs name" style="left:104px;top:99px">Tobin Krasowetz - <small>TN Cases</small></div>
  <div class="stamp" style="left:481px;top:101px">5/27.2017 &nbsp; 12:21 am EDT</div>
  <svg class="kebab" style="left:578px;top:101px" height="9"><circle cx="1" cy="1" r="1" fill="#888"/><circle cx="1" cy="4.5" r="1" fill="#888"/><circle cx="1" cy="8" r="1" fill="#888"/></svg>
  <div class="abs body" style="left:104px;top:115px">Tax implications? And many other questions. Talk to a CPA and Attorney. Along the way take tons of notes.</div>
  <div class="abs reply" style="left:104px;top:134px">Reply</div>
</article>

<article class="abs post" style="top:525px;height:100px">
  <div class="avatar" role="img" aria-label="Profile photo of Mara Ellison" style="left:45px;top:21px;width:19px;height:19px;background:#c47a5e"></div>
  <div class="abs name" style="left:75px;top:23px">Mara Ellison - <small>TN Cases</small></div>
  <div class="stamp" style="left:481px;top:24px">5/27.2017 &nbsp; 12:21 am EDT</div>
  <div class="abs body" style="left:75px;top:45px;width:540px">Step one for most of us os to research what type of corporate structure to start with...We recommend doing your research with an eye toward the future. Will you be raising money through a VC or angels? Will you have partners?</div>
  <div class="abs reply" style="left:75px;top:74px">Reply</div>
</article>

<div class="abs composer"><span>Type text here</span></div>
<div class="abs tool" style="left:1038px"><svg width="20" height="20" viewBox="0 0 20 20"><path d="M7 13l6-6M8.5 8.5l-2 2a2 2 0 003 3l2-2M11.5 11.5l2-2a2 2 0 00-3-3l-2 2" stroke="#fff" stroke-width="1.3" fill="none"/></svg></div>
<div class="abs tool" style="left:1068px"><svg width="20" height="20" viewBox="0 0 20 20"><rect x="4.5" y="7" width="11" height="8" rx="1.5" fill="none" stroke="#fff" stroke-width="1.3"/><circle cx="10" cy="11" r="2.2" fill="none" stroke="#fff" stroke-width="1.3"/><path d="M8 7l1-1.5h2L12 7" stroke="#fff" stroke-width="1.2" fill="none"/></svg></div>
<div class="abs tool" style="left:1098px"><svg width="20" height="20" viewBox="0 0 20 20"><path d="M12.5 6.5l-5 5a1.5 1.5 0 002 2l5.5-5.5a3 3 0 00-4-4L5.5 9.5" stroke="#fff" stroke-width="1.3" fill="none"/></svg></div>
<div class="abs tool" style="left:1129px"><svg width="20" height="20" viewBox="0 0 20 20"><path d="M6.5 4.5h5l2.5 2.5v8.5h-7.5z" fill="none" stroke="#fff" stroke-width="1.3"/><path d="M8.5 9.5h4M8.5 11.5h4M8.5 13.5h3" stroke="#fff" stroke-width="1"/></svg></div>

</body>
</html>
```